CM Candle Tube Packaging Design

Website: www.corvelmare.example
IG: @corvel.mare
Tagline: Elevate Your Ambiance
My brand is a sophisticated brand with luxury candles made of coconut wax. Im looking for an upscale minimalist chic design.
Discover the transformative power of positive energy with Corvel Mare candles. Indulge in true luxury with our specially crafted coconut wax blend that not only ignites captivating scents but also embodies modern elegance and empowering elements.
At Corvel Mare we're committed to delivering a unique and exhilarating aromatic experience to all candle lovers. Each candle is meticulously handcrafted in small batches using luxury fragrance oils exclusively formulated for coconut wax.
Our candles are:
Clean-burning
Paraben-Free
Phthalate-Free
Skin-Safe
Pet-Friendly

```html
<!DOCTYPE html>
<html lang="en">
<head>
<meta charset="utf-8">
<title>CM Candle Tube Packaging</title>
<link rel="stylesheet" href="https://fonts.googleapis.com/css2?family=Montserrat:ital,wght@0,300;0,400;0,500;1,400&family=Mrs+Saint+Delafield&display=swap">
<style>
  :root {
    --backdrop: #f4dde7;
    --tube-pink: #e4aebd;
    --tube-pink-deep: #d79fb0;
    --band-white: #fbf6f8;
    --band-tint: #f2cfdb;
    --lid-white: #f7f8f8;
    --lid-rim: #ffffff;
    --ink: #1c1517;
    --ink-soft: #2e2427;
    --label-white: #ffffff;
    --icon-tone: #f7dde5;
    --icon-text: #fbe9ef;
  }
  * { box-sizing: border-box; margin: 0; padding: 0; }
  html, body {
    width: 1200px; height: 762px; overflow: hidden;
    background: var(--backdrop);
    font-family: "Montserrat", sans-serif;
    color: var(--ink);
  }
  .canvas { position: relative; width: 1200px; height: 762px; }

  .tube {
    position: absolute; top: 100px; width: 310px; height: 588px;
    border-radius: 6px; overflow: hidden;
    background: linear-gradient(90deg, var(--tube-pink) 0%, var(--tube-pink-deep) 60%, var(--tube-pink) 100%);
  }
  .tube--front { left: 75px; }
  .tube--back { left: 455px; }

  .cap-band {
    position: absolute; top: 0; left: 0; right: 0; height: 196px;
    background: linear-gradient(180deg, var(--band-white) 0%, var(--band-tint) 100%);
  }

  /* front face: positions are relative to the tube */
  .front-label > * { position: absolute; left: 0; right: 0; text-align: center; }
  .brand-name {
    top: 306px; line-height: 38px;
    font-weight: 300; font-size: 35px; letter-spacing: 1px;
  }
  .product-line {
    top: 355px; line-height: 14px;
    display: flex; align-items: center; justify-content: center; gap: 8px;
    font-size: 10.5px; font-weight: 400; letter-spacing: 4px;
  }
  .product-line::before, .product-line::after {
    content: ""; width: 14px; height: 1px; background: var(--ink);
  }
  .script-line {
    top: 372px; line-height: 22px;
    font-family: "Mrs Saint Delafield", cursive;
    font-size: 19px; color: var(--ink-soft);
  }
  .tagline-wrap { top: 464px; }
  .tagline {
    display: inline-block; width: 186px; height: 30px; line-height: 30px;
    background: var(--label-white);
    font-size: 9.5px; letter-spacing: 3px; font-weight: 400;
  }
  .net-weight { top: 532px; line-height: 16px; font-size: 10.5px; font-weight: 400; }

  /* back face */
  .back-label > * {
    position: absolute; left: 50px; right: 50px;
    text-align: center; font-size: 7.6px; line-height: 10px;
  }
  .story-intro { top: 244px; }
  .story-promise { top: 300px; }
  .claims {
    top: 338px; display: flex; justify-content: space-between; list-style: none;
  }
  .claims li::before { content: "•"; margin-right: 2px; }
  .story-close { top: 358px; }
  .badges {
    top: 404px; left: 56px; right: 56px;
    display: flex; justify-content: space-between; list-style: none;
  }
  .badge { width: 46px; color: var(--icon-text); font-size: 7.4px; line-height: 9.5px; }
  .badge-mark {
    display: block; width: 26px; height: 28px; margin: 0 auto 6px;
    border-radius: 50%; background: var(--icon-tone); opacity: 0.8;
  }
  .contact { top: 480px; font-style: italic; font-size: 8.8px; line-height: 12px; }
  .batch-note { top: 507px; font-style: italic; font-size: 8.8px; line-height: 12px; }

  .lid {
    position: absolute; left: 822px; top: 273px;
    width: 300px; height: 300px; border-radius: 50%;
    background: var(--lid-rim);
    display: flex; align-items: center; justify-content: center;
  }
  .lid-face {
    width: 276px; height: 276px; border-radius: 50%;
    background: var(--lid-white);
    display: flex; align-items: center; justify-content: center;
  }
  .lid-monogram { font-weight: 300; font-size: 62px; letter-spacing: 2px; }
</style>
</head>
<body>
<main class="canvas">

  <section class="tube tube--front">
    <div class="cap-band" role="img" aria-label="Repeating pattern of soft pink flame outlines on white"></div>
    <div class="front-label">
      <h1 class="brand-name">CORVEL MARE</h1>
      <p class="product-line">HANDMADE CANDLES</p>
      <p class="script-line">with purpose and love</p>
      <div class="tagline-wrap"><p class="tagline">Elevate Your Ambiance</p></div>
      <p class="net-weight">9 OZ/255G</p>
    </div>
  </section>

  <section class="tube tube--back">
    <div class="cap-band" role="img" aria-label="Repeating pattern of soft pink flame outlines on white"></div>
    <div class="back-label">
      <p class="story-intro">At Corvel Mare, we believe that positive energy can move mountains. We strive to elevate that energy in every way possible. Our coconut wax combination creates an enticing scent with no compromises modern, classy aromas with empowering elements.</p>
      <p class="story-promise">We believe that candle lovers deserve only the best. Our candles are made from luxury fragrance oil specially formulated for coconut wax and are:</p>
      <ul class="claims">
        <li>Clean</li>
        <li>Paraben Free</li>
        <li>Skin Safe</li>
        <li>Pet Friendly</li>
      </ul>
      <p class="story-close">Nothing says luxury and class quite like being able to create your own perfect scent in the comfort of your own home.</p>
      <ul class="badges">
        <li class="badge"><span class="badge-mark" role="img" aria-label="Hand icon"></span>HAND POURED</li>
        <li class="badge"><span class="badge-mark" role="img" aria-label="Leaf bowl icon"></span>VEGAN</li>
        <li class="badge"><span class="badge-mark" role="img" aria-label="Globe icon"></span>ECO FRIENDLY</li>
        <li class="badge"><span class="badge-mark" role="img" aria-label="Flower icon"></span>UNIQUELY SCENTED</li>
      </ul>
      <p class="contact">www.corvelmare.example<br>@corvel.mare</p>
      <p class="batch-note">Made with love in small batches.</p>
    </div>
  </section>

  <section class="lid">
    <div class="lid-face">
      <span class="lid-monogram">CM</span>
    </div>
  </section>

</main>
</body>
</html>
```